Timber Crest Construction Needs business card

Hey we are in need of business card designs. I have upload our logo as a guideline, but free feel to run with it or come up with something unique.
Pls have fun with it and be creative. the name says it all!
i will give some directions after i see a few entries..
Updates
Logo source file has been uploaded..
Hey because of the logo is so colourful already.
Can we have a few submissions with less colour.
Also we are looking for clever/hidden/descriptive business card.

```html
<!DOCTYPE html>
<html lang="en">
<head>
<meta charset="utf-8">
<title>Timber Crest Construction – Business Card</title>
<link rel="stylesheet" href="https://fonts.googleapis.com/css2?family=Open+Sans:wght@400;600;700&display=swap">
<style>
  :root {
    --page-bg: #e9e7e4;
    --card-bg: #ffffff;
    --ink-grey: #585e62;
    --ink-dark: #2b2b2b;
    --accent-blue: #2d6aa6;
    --band-blue: #5aa6e6;
    --band-dark: #4b5157;
    --rule-blue: #8fc0ea;
  }
  * { box-sizing: border-box; margin: 0; padding: 0; }
  html, body { width: 1200px; height: 470px; overflow: hidden; }
  body {
    background: var(--page-bg);
    font-family: "Open Sans", Arial, sans-serif;
    color: var(--ink-dark);
    position: relative;
  }
  .card {
    position: absolute;
    top: 85px;
    width: 520px;
    height: 300px;
    background: var(--card-bg);
    box-shadow: 0 4px 14px rgba(0,0,0,0.18);
    overflow: hidden;
  }
  .card--front { left: 40px; }
  .card--back { left: 640px; }

  .wordmark {
    position: absolute;
    left: 0; right: 0;
    display: flex;
    align-items: center;
    justify-content: center;
    gap: 10px;
    color: var(--ink-grey);
    font-weight: 700;
    text-transform: uppercase;
    letter-spacing: 0.5px;
    white-space: nowrap;
  }
  .wordmark__square { background: var(--ink-grey); flex: none; }
  .card--front .wordmark { top: 62px; font-size: 22px; }
  .card--front .wordmark__square { width: 16px; height: 16px; }
  .card--back .wordmark { top: 128px; font-size: 31px; }
  .card--back .wordmark__square { width: 22px; height: 22px; }

  .person {
    position: absolute;
    right: 262px;
    top: 160px;
    text-align: right;
  }
  .person__name { color: var(--accent-blue); font-weight: 700; font-size: 16px; line-height: 1.1; }
  .person__title { color: var(--accent-blue); font-weight: 700; font-size: 12px; margin-bottom: 10px; }
  .person__address { font-size: 12px; line-height: 1.35; }

  .divider {
    position: absolute;
    left: 268px;
    top: 145px;
    width: 1.5px;
    height: 95px;
    background: var(--rule-blue);
  }

  .contacts {
    position: absolute;
    left: 282px;
    top: 148px;
    list-style: none;
    font-size: 12.5px;
    line-height: 1;
  }
  .contacts li { display: flex; align-items: center; gap: 6px; height: 21px; }
  .contacts svg { width: 11px; height: 11px; flex: none; fill: var(--ink-dark); }

  .bands { position: absolute; left: 0; bottom: 0; width: 520px; height: 70px; }
</style>
</head>
<body>

<section class="card card--front">
  <div class="wordmark">
    <span class="wordmark__square"></span>
    <span class="wordmark__name">Timber Crest Construction</span>
  </div>

  <div class="person">
    <p class="person__name">Your Name</p>
    <p class="person__title">Title</p>
    <p class="person__address">Street Name City Name<br>State Zipcode</p>
  </div>

  <div class="divider"></div>

  <ul class="contacts">
    <li>
      <svg viewBox="0 0 24 24"><path d="M6.6 10.8a15 15 0 0 0 6.6 6.6l2.2-2.2a1 1 0 0 1 1-.25 11.4 11.4 0 0 0 3.6.57 1 1 0 0 1 1 1V20a1 1 0 0 1-1 1A17 17 0 0 1 3 4a1 1 0 0 1 1-1h3.5a1 1 0 0 1 1 1c0 1.25.2 2.45.57 3.57a1 1 0 0 1-.25 1z"/></svg>
      0400 555 181
    </li>
    <li>
      <svg viewBox="0 0 24 24"><path d="M6.6 10.8a15 15 0 0 0 6.6 6.6l2.2-2.2a1 1 0 0 1 1-.25 11.4 11.4 0 0 0 3.6.57 1 1 0 0 1 1 1V20a1 1 0 0 1-1 1A17 17 0 0 1 3 4a1 1 0 0 1 1-1h3.5a1 1 0 0 1 1 1c0 1.25.2 2.45.57 3.57a1 1 0 0 1-.25 1z"/></svg>
      0400 555 181
    </li>
    <li>
      <svg viewBox="0 0 24 24"><path d="M2 5h20v14H2z M2 5l10 8 10-8" fill="none" stroke="#2b2b2b" stroke-width="2.5"/></svg>
      office@timbercrestbuild.com
    </li>
    <li>
      <svg viewBox="0 0 24 24"><circle cx="12" cy="12" r="9.5" fill="none" stroke="#2b2b2b" stroke-width="2"/><path d="M2.5 12h19M12 2.5c-3.5 4-3.5 15 0 19M12 2.5c3.5 4 3.5 15 0 19" fill="none" stroke="#2b2b2b" stroke-width="1.6"/></svg>
      www.timbercrestbuild.com
    </li>
  </ul>

  <svg class="bands" viewBox="0 0 520 70" preserveAspectRatio="none" aria-hidden="true">
    <polygon points="0,70 0,56 240,44 226,70" fill="var(--band-dark)"/>
    <polygon points="240,56 520,24 520,38 252,70 232,70" fill="var(--band-blue)"/>
  </svg>
</section>

<section class="card card--back">
  <div class="wordmark">
    <span class="wordmark__square"></span>
    <span class="wordmark__name">Timber Crest<br>Construction</span>
  </div>
</section>

</body>
</html>
```